A design led business card for the construction industry

High-end business card to match logo. White logo on dark grey/off black to the front. Matching dark font on white to back, possibly with logo design again.

We offer construction and project management services to commercial and private clients in the UK. Projetcs range from newbuilds, conversion of listed buildings and refurbishments and extensions of existing homes. Our focus is on quality and attention to detail using the highest skills.

Contact Information for Business Card

Name; Dorian Keble BSc
Position; Project Manager
Mobile; 07962 408 175
Tel; 01632 960457
email; dorian@stonevale.co.uk
web; www.stonevale.co.uk
Address; Kestlow on Avern, KX4 7PW

Colors

Designer to choose only greyscale colors for use in the design.

Requirements
Must have
• To include the below description of the business,

CONSTRUCTION - PROJECT MANAGEMENT
Nice to have
• The posibility of the top back of the card being used as a ruler. So will have a measurement to scale in mm or an architect scale of 1:50
Should not have
• Should not be portrait

```html
<!DOCTYPE html>
<html lang="en">
<head>
<meta charset="utf-8">
<title>Stonevale – Business Card</title>
<link href="https://fonts.googleapis.com/css2?family=Arimo:wght@400;700&display=swap" rel="stylesheet">
<style>
  :root {
    --page-bg: #e4e4e4;
    --card-bg: #f7f5f5;
    --ink: #111111;
    --rule: #3a3a3a;
    --tick: #333333;
    --band: #000000;
    --band-text: #ffffff;
  }
  * { margin: 0; padding: 0; box-sizing: border-box; }
  html, body {
    width: 1200px; height: 900px; overflow: hidden;
    background: var(--page-bg);
    font-family: "Arimo", Arial, sans-serif;
    color: var(--ink);
  }
  .card {
    position: absolute; left: 100px; top: 142px;
    width: 1000px; height: 616px;
    background: var(--card-bg);
    box-shadow: 0 6px 24px rgba(0,0,0,0.18);
    overflow: hidden;
  }
  .ruler { position: absolute; left: 0; top: 0; width: 1000px; height: 52px; }
  .brand {
    position: absolute; left: 58px; top: 192px; width: 400px;
    text-align: center;
  }
  .brand-square {
    width: 150px; height: 150px; margin: 0 auto 46px;
    border: 5px solid var(--ink);
  }
  .brand-name {
    font-size: 34px; font-weight: 400; letter-spacing: 16px;
    padding-left: 16px; line-height: 1;
  }
  .divider {
    position: absolute; left: 504px; top: 165px;
    width: 1.5px; height: 288px; background: var(--rule);
  }
  .contact { position: absolute; left: 543px; top: 152px; }
  .contact-name { font-size: 31px; font-weight: 700; line-height: 38px; }
  .contact-name .cred { font-weight: 400; }
  .contact-role { font-size: 26px; line-height: 30px; }
  .contact-list { list-style: none; margin-top: 30px; }
  .contact-list li {
    display: flex; align-items: center; gap: 10px;
    font-size: 27px; line-height: 36.5px;
  }
  .contact-list svg { width: 26px; height: 26px; flex: none; }
  .contact-address { font-size: 27px; margin-top: 26px; }
  .tagline-band {
    position: absolute; left: 0; bottom: 0; width: 1000px; height: 93px;
    background: var(--band); color: var(--band-text);
    display: flex; align-items: center; justify-content: center;
    font-size: 34px; letter-spacing: 0.3px;
  }
</style>
</head>
<body>
  <div class="card">
    <svg class="ruler" viewBox="0 0 1000 52" aria-hidden="true">
      <defs>
        <pattern id="ruler-scale" x="4" y="0" width="83.5" height="52" patternUnits="userSpaceOnUse">
          <line x1="0.9" y1="0" x2="0.9" y2="50" stroke="#333" stroke-width="1.8"/>
          <line x1="17.6" y1="0" x2="17.6" y2="14" stroke="#333" stroke-width="1.4"/>
          <line x1="34.3" y1="0" x2="34.3" y2="24" stroke="#333" stroke-width="1.4"/>
          <line x1="51" y1="0" x2="51" y2="14" stroke="#333" stroke-width="1.4"/>
          <line x1="67.7" y1="0" x2="67.7" y2="24" stroke="#333" stroke-width="1.4"/>
        </pattern>
      </defs>
      <line x1="0" y1="1" x2="1000" y2="1" stroke="#333" stroke-width="2"/>
      <rect width="1000" height="52" fill="url(#ruler-scale)"/>
    </svg>

    <div class="brand">
      <div class="brand-square"></div>
      <div class="brand-name">STONEVALE</div>
    </div>

    <div class="divider"></div>

    <div class="contact">
      <div class="contact-name">DORIAN KEBLE <span class="cred">BSc</span></div>
      <div class="contact-role">Project Manager</div>
      <ul class="contact-list">
        <li>
          <svg viewBox="0 0 24 24" aria-hidden="true"><rect x="6" y="2" width="12" height="20" rx="2" fill="none" stroke="#111" stroke-width="2"/><line x1="10" y1="18" x2="14" y2="18" stroke="#111" stroke-width="2"/></svg>
          07962 408 175
        </li>
        <li>
          <svg viewBox="0 0 24 24" aria-hidden="true"><path d="M6 3l3 0 1.5 4.5-2 1.5a11 11 0 0 0 6.5 6.5l1.5-2 4.5 1.5v3a2 2 0 0 1-2 2A17 17 0 0 1 4 5a2 2 0 0 1 2-2z" fill="none" stroke="#111" stroke-width="2" stroke-linejoin="round"/></svg>
          01632 960457
        </li>
        <li>
          <svg viewBox="0 0 24 24" aria-hidden="true"><rect x="2" y="5" width="20" height="14" fill="#111"/><path d="M2 5l10 8 10-8M2 19l7.5-7M22 19l-7.5-7" fill="none" stroke="#f7f5f5" stroke-width="1.5"/></svg>
          dorian@stonevale.co.uk
        </li>
        <li>
          <svg viewBox="0 0 24 24" aria-hidden="true"><circle cx="12" cy="12" r="10" fill="none" stroke="#111" stroke-width="2"/><ellipse cx="12" cy="12" rx="4.5" ry="10" fill="none" stroke="#111" stroke-width="1.6"/><line x1="2" y1="12" x2="22" y2="12" stroke="#111" stroke-width="1.6"/><line x1="4" y1="7" x2="20" y2="7" stroke="#111" stroke-width="1.4"/><line x1="4" y1="17" x2="20" y2="17" stroke="#111" stroke-width="1.4"/></svg>
          www.stonevale.co.uk
        </li>
      </ul>
      <div class="contact-address">Kestlow on Avern, KX4 7PW</div>
    </div>

    <div class="tagline-band">CONSTRUCTION - PROJECT MANAGEMENT</div>
  </div>
</body>
</html>
```